Accounting firm for Dentists needs a brochure

We are an accounting firm that specializes in dental practices. We have the information we want attached in a word file. We don't care the number of folds. We would just like it to look professional. Our logo is also attached so you know what our company colors are.

Accounting

```html
<!DOCTYPE html>
<html lang="en">
<head>
<meta charset="utf-8">
<title>Brightline Dental CPAs – Trifold Brochure</title>
<link rel="stylesheet" href="https://fonts.googleapis.com/css2?family=Cinzel:wght@700&family=Open+Sans:wght@400;600;700&display=swap">
<style>
  :root{
    --page:#e9e6e1;
    --sun:#f3d321;
    --sun-soft:#f1e58a;
    --mist:#d9eee0;
    --sky:#6fc9dc;
    --ink:#1b1b1b;
    --navy:#1f3a5c;
    --brand:#2a9fd8;
    --paper:#ffffff;
    --photo-warm:#c9b89a;
    --photo-cool:#3a5d86;
  }
  *{box-sizing:border-box;margin:0;padding:0}
  html,body{width:1200px;height:1020px;overflow:hidden;background:var(--page)}
  body{font-family:"Open Sans",Arial,sans-serif;color:var(--ink)}
  .sheet{position:absolute;left:60px;display:flex;box-shadow:0 6px 18px rgba(0,0,0,.18)}
  .sheet--inside{top:30px}
  .sheet--outside{top:525px;left:240px}
  .panel{width:360px;height:465px;padding:18px 26px;position:relative;
    background:linear-gradient(180deg,var(--sun) 0%,var(--sun-soft) 30%,var(--mist) 62%,var(--sky) 100%);
    border-right:1px solid rgba(0,0,0,.06);display:flex;flex-direction:column;align-items:center}
  .panel:last-child{border-right:none}
  .panel-title{font-family:"Cinzel",Georgia,serif;font-size:19px;font-weight:700;letter-spacing:.5px;margin-bottom:6px;text-align:center}
  .section-title{font-weight:700;font-size:13.5px;text-transform:uppercase;text-align:center;margin:6px 0 2px}
  .copy{font-size:12.5px;line-height:1.32;text-align:justify;text-align-last:center}
  .photo{width:100%;border-radius:10px;margin:8px 0}
  .photo--target{height:82px;background:radial-gradient(circle at 60% 50%,#f4f4f4 0,#d8d8d8 55%,#bdbdbd 100%)}
  .photo--clock{height:80px;background:linear-gradient(90deg,#1e2f4d,var(--photo-cool) 55%,#1a2b45)}
  .photo--tax{height:96px;background:radial-gradient(circle at 50% 55%,#4a8aa0 0,#b9d2d8 45%,#f3efe3 80%)}
  .photo--tools{height:110px;margin-top:auto;background:linear-gradient(180deg,#f5f8f6,#e2ecea)}
  .photo--wallclock{height:70px;background:linear-gradient(135deg,#f1f1ea,#cfd7c8)}
  .photo--calculator{height:110px;margin-top:auto;background:linear-gradient(160deg,#7a8590,#2e3540)}
  .logo-card{background:var(--paper);width:230px;padding:20px 14px;border-radius:4px;text-align:center;margin:8px 0 34px;box-shadow:0 1px 4px rgba(0,0,0,.15)}
  .logo-name{font-family:"Open Sans",Arial,sans-serif;font-weight:700;font-size:24px;line-height:1.15;color:var(--brand)}
  .cover-copy{font-size:17px;line-height:1.4;text-align:center}
  .cover-copy strong{font-weight:700}
  .contact{margin-top:auto;text-align:center;font-size:14px;line-height:1.5}
  .contact-line{font-weight:700;letter-spacing:1px}
  .back-lead{font-size:15px;line-height:1.4;text-align:center;margin-top:20px}
</style>
</head>
<body>

<section class="sheet sheet--inside" aria-label="Brochure inside">
  <article class="panel panel--outsource">
    <h2 class="panel-title">Reasons To Outsource</h2>
    <h3 class="section-title">Time</h3>
    <p class="copy">Our virtual accounting services will save you valuable time that can be used to focus on growing your business. Bookkeeping, payroll and other accounting tasks are a burden and a distraction from your future.</p>
    <div class="photo photo--wallclock" role="img" aria-label="Photo of a wall clock"></div>
    <h3 class="section-title">Cost</h3>
    <p class="copy">Outsourcing can cost up to 35% less than hiring an in-house accountant or bookkeeper, letting you invest more in your practice where it matters.</p>
    <div class="photo photo--calculator" role="img" aria-label="Photo of a calculator keypad"></div>
  </article>

  <article class="panel panel--commitment">
    <h2 class="panel-title">Our Commitment</h2>
    <div class="photo photo--target" role="img" aria-label="Photo of a dartboard target with arrows and a house shape"></div>
    <h3 class="section-title">Excellence</h3>
    <p class="copy">We strive to exceed your expectations as an accounting firm, by anticipating your financial needs and providing guidance throughout the year. Our staff are all licensed CPA's with experience in several industries so we are well-equipped to handle any complex accounting issues.</p>
    <div class="photo photo--clock" role="img" aria-label="Photo of a hand presenting a glowing clock"></div>
    <h3 class="section-title">Timeliness</h3>
    <p class="copy">To make sound financial decisions, it is pertinent that records are maintained and analyzed monthly. We maintain your books on a monthly-basis, as well as calculate your estimated tax liability so there are no surprises at year-end.</p>
  </article>

  <article class="panel panel--strategy">
    <h3 class="section-title">Advanced Tax Strategies</h3>
    <p class="copy">Tax planning should be more than just finding out what you owe in advance. At Brightline Dental CPAs, we pride ourselves in advising in areas of advanced tax mitigation strategies, to reduce your overall tax bill - not just predict it.</p>
    <div class="photo photo--tax" role="img" aria-label="Illustration of an umbrella sheltering a small house from falling tax words"></div>
    <h3 class="section-title">Personalization</h3>
    <p class="copy">Every practice has different accounting needs, so we work closely with you to understand your specific financial and tax situations. Our services are tailored to guide you to meet your specific financial objectives.</p>
    <div class="photo photo--tools" role="img" aria-label="Photo of dental instruments and a toothbrush"></div>
  </article>
</section>

<section class="sheet sheet--outside" aria-label="Brochure outside">
  <article class="panel panel--back">
    <p class="back-lead">Why not schedule a free consultation? Let us handle your finances so you can focus on your patients.</p>
    <div class="contact">
      <p>Call or email us today to arrange a meeting.</p>
      <p class="contact-line">1-800-555-0142</p>
      <p class="contact-line">info@brightlinedentalcpa.com</p>
    </div>
  </article>

  <article class="panel panel--cover">
    <div class="logo-card">
      <p class="logo-name">Brightline Dental CPAs</p>
    </div>
    <p class="cover-copy">At <strong>Brightline Dental CPAs</strong>, our licensed CPA's have the knowledge to tackle complex tax and accounting issues and the experience to present a clear picture of your financial position.</p>
  </article>
</section>

</body>
</html>
```